Brellwick Partners, LLC Stationary

Brellwick Partners, LLC is a new financial planning and consulting company. We are looking for designs on business cards, letterhead, envelopes, and anything else that would be useful. Our preference for business card design is two sided. We are looking for a professional and clean look with incorporating the logo and patriotic feel. Thank you to all who participate and good luck!

```html
<!DOCTYPE html>
<html lang="en">
<head>
<meta charset="utf-8">
<title>Brellwick Partners, LLC – Business Card</title>
<link rel="stylesheet" href="https://fonts.googleapis.com/css2?family=Saira:wght@400;500;600&display=swap">
<style>
  :root {
    --navy: #173e6e;
    --navy-deep: #0f2f57;
    --red: #c8232f;
    --white: #ffffff;
    --paper: #ebe8e3;
    --ink-soft: #dfe6ef;
    --grey: #6b7380;
  }
  html, body {
    margin: 0;
    width: 1200px;
    height: 950px;
    overflow: hidden;
    background: var(--paper);
    font-family: "Saira", Arial, sans-serif;
  }
  .canvas {
    width: 1200px;
    height: 950px;
    display: flex;
    flex-direction: column;
    align-items: center;
    justify-content: center;
    gap: 50px;
  }
  .card {
    position: relative;
    width: 700px;
    height: 400px;
    box-shadow: 0 10px 28px rgba(0,0,0,0.18);
    overflow: hidden;
  }

  /* Front */
  .card--front {
    background: linear-gradient(160deg, var(--navy) 0%, var(--navy-deep) 100%);
    color: var(--white);
  }
  .front__band {
    position: absolute;
    top: 0; right: 0;
    width: 250px;
    height: 100%;
    background: var(--red);
  }
  .front__identity {
    position: absolute;
    left: 48px;
    top: 60px;
  }
  .holder-name {
    margin: 0;
    font-size: 30px;
    font-weight: 500;
    letter-spacing: 0.04em;
    text-transform: uppercase;
    color: var(--red);
    line-height: 1.1;
  }
  .holder-title {
    margin: 4px 0 0;
    font-size: 22px;
    font-weight: 400;
    letter-spacing: 0.05em;
    text-transform: uppercase;
    color: var(--ink-soft);
  }
  .front__contact {
    position: absolute;
    left: 48px;
    bottom: 44px;
    margin: 0;
    padding: 0;
    list-style: none;
    font-size: 17px;
    line-height: 1.5;
    color: var(--white);
  }
  .front__contact .address { margin-bottom: 12px; }
  .contact-line {
    display: flex;
    align-items: center;
    gap: 10px;
  }
  .contact-icon {
    width: 14px;
    height: 14px;
    flex: none;
  }

  /* Back */
  .card--back {
    background: var(--white);
    display: flex;
    flex-direction: column;
    align-items: center;
    justify-content: center;
    gap: 14px;
  }
  .brand-name {
    display: flex;
    align-items: center;
    gap: 14px;
    margin: 0;
    font-size: 40px;
    font-weight: 600;
    letter-spacing: 0.03em;
    color: var(--navy);
  }
  .brand-name .mark {
    width: 18px;
    height: 18px;
    background: var(--red);
  }
  .brand-rule {
    width: 360px;
    height: 2px;
    background: var(--red);
  }
  .tagline {
    margin: 0;
    font-size: 14px;
    font-weight: 400;
    letter-spacing: 0.22em;
    text-transform: uppercase;
    color: var(--grey);
  }
</style>
</head>
<body>
<main class="canvas">

  <section class="card card--front" aria-label="Business card front">
    <div class="front__band"></div>
    <div class="front__identity">
      <h1 class="holder-name">Dana Whitford</h1>
      <p class="holder-title">CEO/Founder</p>
    </div>
    <ul class="front__contact">
      <li class="address">4120 Larkspur Way<br>Fairbanks, Alaska 99701</li>
      <li class="contact-line">
        <svg class="contact-icon" viewBox="0 0 24 24"><circle cx="12" cy="12" r="12" fill="#c8232f"/><path d="M8 6.5l2 .2 1 3-1.4 1.2a8 8 0 0 0 3.5 3.5l1.2-1.4 3 1 .2 2c0 .8-.7 1.5-1.5 1.4A11 11 0 0 1 6.6 8c-.1-.8.6-1.5 1.4-1.5z" fill="#fff"/></svg>
        555 214 0387
      </li>
      <li class="contact-line">
        <svg class="contact-icon" viewBox="0 0 24 24"><circle cx="12" cy="12" r="12" fill="#c8232f"/><rect x="8" y="5" width="8" height="14" rx="1.5" fill="#fff"/><rect x="9.5" y="7" width="5" height="8" fill="#c8232f"/></svg>
        555 380 6142
      </li>
      <li class="contact-line">
        <svg class="contact-icon" viewBox="0 0 24 24"><circle cx="12" cy="12" r="12" fill="#c8232f"/><rect x="6" y="8" width="12" height="8" fill="#fff"/><path d="M6 8l6 5 6-5" fill="none" stroke="#c8232f" stroke-width="1.3"/></svg>
        hello@brellwick.com
      </li>
      <li class="contact-line">
        <svg class="contact-icon" viewBox="0 0 24 24"><circle cx="12" cy="12" r="12" fill="#c8232f"/><circle cx="12" cy="12" r="6" fill="none" stroke="#fff" stroke-width="1.5"/><path d="M6 12h12M12 6c-3 3-3 9 0 12M12 6c3 3 3 9 0 12" fill="none" stroke="#fff" stroke-width="1.2"/></svg>
        www.brellwick.com
      </li>
    </ul>
  </section>

  <section class="card card--back" aria-label="Business card back">
    <h2 class="brand-name"><span class="mark"></span>Brellwick Partners, LLC</h2>
    <div class="brand-rule"></div>
    <p class="tagline">Financial Planning and Consulting</p>
  </section>

</main>
</body>
</html>
```